New Business Card Design Project

Use the flyer uploaded and website www.brightoakbuilders.com for inspiration.
List Our Services on Backside of business cards
Marcus Delling
Harborline Builders Inc.
Licensed General Contractors
858-471-6093

Contact Information for Business Card

Use the flyer uploaded and website www.brightoakbuilders.com for inspiration. List Our Services on Backside of business cards Marcus Delling Harborline Builders Inc. Licensed General Contractors 858-471-6093

```html
<!DOCTYPE html>
<html lang="en">
<head>
<meta charset="utf-8">
<title>Harborline Builders – Business Card</title>
<link href="https://fonts.googleapis.com/css2?family=Cinzel:wght@400&family=Montserrat:wght@400;500;800&display=swap" rel="stylesheet">
<style>
  :root {
    --bg: #e6e4e2;
    --card-white: #ffffff;
    --card-black: #141414;
    --band-dark: #1c1c1c;
    --band-grey: #8a8a8a;
    --ink: #151515;
    --ink-soft: #444444;
    --paper-text: #f2f2f2;
  }
  * { margin: 0; padding: 0; box-sizing: border-box; }
  html, body { width: 1200px; height: 786px; overflow: hidden; }
  body {
    background: var(--bg);
    font-family: "Montserrat", sans-serif;
    position: relative;
  }
  .card {
    position: absolute;
    top: 239px;
    width: 540px;
    height: 308px;
    box-shadow: 0 10px 30px rgba(0,0,0,.18);
    overflow: hidden;
  }
  .card--front { left: 40px; background: var(--card-white); }
  .card--back { left: 620px; background: var(--card-black); }

  .card__bands { position: absolute; inset: 0; }

  .brand-name {
    position: absolute;
    font-family: "Cinzel", serif;
    font-weight: 400;
    letter-spacing: 1px;
    white-space: nowrap;
  }
  .card--front .brand-name {
    left: 230px; top: 96px; width: 290px;
    text-align: center; font-size: 26px; color: var(--ink);
  }
  .card--back .brand-name {
    left: 24px; top: 138px; width: 290px;
    text-align: center; font-size: 26px; color: var(--paper-text);
  }

  .phone {
    position: absolute; left: 330px; top: 188px;
    display: flex; align-items: center; gap: 12px;
    color: #fff; font-size: 16px; font-weight: 400; letter-spacing: .5px;
  }
  .license {
    position: absolute; left: 340px; top: 240px;
    font-size: 14px; color: var(--ink); letter-spacing: .3px;
  }
  .person { position: absolute; left: 30px; top: 176px; }
  .person__name { font-size: 26px; font-weight: 800; color: var(--ink); line-height: 1.05; }
  .person__title { font-size: 14px; color: var(--ink-soft); margin-top: 2px; }
  .website {
    position: absolute; left: 26px; top: 272px;
    display: flex; align-items: center; gap: 10px;
    color: #fff; font-size: 14px; letter-spacing: .3px;
  }

  .services {
    position: absolute; left: 330px; top: 72px;
    list-style: none; color: var(--paper-text);
    font-size: 12px; line-height: 1.5;
  }
  .services li::before { content: "•"; margin-right: 7px; }
</style>
</head>
<body>
  <section class="card card--front" aria-label="Business card front">
    <svg class="card__bands" width="540" height="308" viewBox="0 0 540 308" aria-hidden="true">
      <polygon points="312,176 540,176 540,224 302,224" fill="#1c1c1c"/>
      <polygon points="0,252 296,252 285,308 0,308" fill="#8a8a8a"/>
    </svg>
    <div class="brand-name">Harborline Builders</div>
    <div class="phone">
      <svg width="16" height="16" viewBox="0 0 24 24" aria-hidden="true"><path fill="#fff" d="M6.6 10.8a15.1 15.1 0 0 0 6.6 6.6l2.2-2.2a1 1 0 0 1 1-.25 11.4 11.4 0 0 0 3.6.57 1 1 0 0 1 1 1V20a1 1 0 0 1-1 1A17 17 0 0 1 3 4a1 1 0 0 1 1-1h3.5a1 1 0 0 1 1 1c0 1.25.2 2.45.57 3.57a1 1 0 0 1-.25 1z"/></svg>
      <span>858-471-6093</span>
    </div>
    <div class="license">CSLB&nbsp; Licensed no #1048265</div>
    <div class="person">
      <div class="person__name">Marcus Delling</div>
      <div class="person__title">Managing Director</div>
    </div>
    <div class="website">
      <svg width="13" height="13" viewBox="0 0 24 24" aria-hidden="true"><circle cx="12" cy="12" r="10" fill="none" stroke="#fff" stroke-width="2.4"/><path d="M2 12h20M12 2c3 3 3 17 0 20M12 2c-3 3-3 17 0 20" fill="none" stroke="#fff" stroke-width="2"/></svg>
      <span>www.brightoakbuilders.com</span>
    </div>
  </section>

  <section class="card card--back" aria-label="Business card back">
    <div class="brand-name">Harborline Builders</div>
    <ul class="services">
      <li>Remodel: Kitchen &amp; Bath</li>
      <li>Painting: Interior &amp; Exterior</li>
      <li>Flooring: Carpet, Vinyl, Wood</li>
      <li>Window &amp; Door Replacement</li>
      <li>Plumbing: Repair &amp; Upgrades</li>
      <li>Energy Efficient Upgrades</li>
      <li>Deck &amp; Patio construction</li>
      <li>Water &amp; Mold Damage</li>
      <li>Garage Renovation</li>
    </ul>
  </section>
</body>
</html>
```